Psychiatric Office Needs a Website- 1st Time Ever!

Been in practice since 2003 with no website, but finally ready to dive in. We are Maplecrest Behavioral Healthcare, a mental health outpatient practice based in Fayetteville, Georgia that sees diverse individuals and families from childhood to advanced age for a variety of conditions. We've grown by word of mouth and referral but would now like to have a digital footprint. Be the pioneer of our website and we will be sure to share. We would like to see designs that are modern, animated, fairly colorful, easy to read, and caters to all ages. Also, we would like the design to take the whole page (not be centered) and can be viewed well on phone/tablet. Please see our outline for more information. Our motto/slogan is: Maplecrest Behavioral Healthcare- A step forward in your wellness journey, so the design should try to reflect that.
Updates

Project Deadline Extended
Reason: site in progress

Target Market(s)

Children through elderly

Industry/Entity Type

Medical

Logo Text

Stepping forward in your wellness journey

Number of Pages Required

1 page

Colors

Designer to choose colors to be used in the design.

Requirements
Must have
• Animation or moving pictures.
• Color.
• Concise.
• User friendly
• Diversity in the stock photos

```html
<!DOCTYPE html>
<html lang="en">
<head>
<meta charset="utf-8">
<title>Maplecrest Behavioral Healthcare</title>
<link href="https://fonts.googleapis.com/css2?family=Lato:wght@300;400;700;900&family=Open+Sans:wght@400;600;700&display=swap" rel="stylesheet">
<style>
:root{
  --teal:#16b2c7;
  --teal-soft:#c9e9ef;
  --green:#6aac2e;
  --dark:#555555;
  --darker:#4a4a4a;
  --ink:#2c2c2c;
  --muted:#8a8a8a;
  --blue:#1b74ba;
  --panel:#f4f5f7;
  --white:#ffffff;
}
*{box-sizing:border-box;margin:0;padding:0}
html,body{width:1200px;height:2687px;overflow:hidden;background:var(--white)}
body{font-family:"Open Sans",Arial,sans-serif;color:var(--ink);position:relative}
.wrap{position:absolute;left:161px;width:878px}
h2,h3,.brand{font-family:"Lato",Arial,sans-serif}

/* top bar */
.topbar{position:absolute;top:0;left:0;width:1200px;height:29px;border-bottom:1px solid #eee}
.topbar .links{position:absolute;left:161px;top:8px;display:flex;gap:20px;font-size:10px;color:#444}
.topbar .social{position:absolute;right:161px;top:9px;display:flex;gap:12px}
.topbar .social span{width:10px;height:10px;border-radius:50%;background:var(--teal)}

/* header */
.header{position:absolute;top:29px;left:0;width:1200px;height:93px}
.logo{position:absolute;left:161px;top:24px;display:flex;align-items:center;gap:10px}
.logo .dot{width:44px;height:44px;border-radius:50%;background:var(--teal)}
.brand{font-size:17px;font-weight:700;color:var(--green);line-height:1.2;width:170px}
.info{position:absolute;top:26px;display:flex;align-items:center;gap:8px;font-size:9.5px;line-height:1.7;color:#444}
.info b{color:var(--ink)}
.info .ic{width:40px;height:40px;border-radius:50%;background:var(--teal);display:flex;align-items:center;justify-content:center}

/* nav */
.nav{position:absolute;top:122px;left:0;width:1200px;height:43px;background:var(--dark)}
.nav ul{list-style:none;position:absolute;left:161px;top:12px;display:flex;gap:30px;font-family:"Lato",Arial,sans-serif;font-weight:700;font-size:14.5px;color:var(--white)}
.nav li.active{color:var(--green)}
.nav .search{position:absolute;right:161px;top:12px}

/* hero */
.hero{position:absolute;top:165px;left:0;width:1200px;height:473px;background:linear-gradient(180deg,#6f7a7e 0%,#8b9187 35%,#8e9457 62%,#b6b14a 85%,#9b9a3e 100%)}
.hero h1{position:absolute;left:161px;top:100px;font-family:"Lato",Arial,sans-serif;font-weight:700;font-size:31px;color:var(--white)}
.hero p{position:absolute;left:161px;top:142px;font-family:"Lato",Arial,sans-serif;font-weight:300;font-size:31px;line-height:1.3;color:var(--white);width:360px}
.btn-green{position:absolute;left:161px;top:290px;background:var(--green);color:var(--white);font-size:14px;font-weight:600;padding:11px 18px;border-radius:5px}
.slider{position:absolute;left:526px;top:399px;display:flex;gap:8px}
.slider span{width:42px;height:3px;background:#cfcfcf}
.slider span.on{background:var(--green)}

/* section title */
.title{font-family:"Lato",Arial,sans-serif;font-weight:700;letter-spacing:2px;font-size:30px}
.rule{width:60px;height:3px;background:var(--teal)}

/* about */
.about{top:666px;height:274px}
.about .title{position:absolute;left:0;top:26px}
.about .rule{position:absolute;left:0;top:74px}
.about p{position:absolute;left:0;top:100px;width:430px;font-size:12.5px;line-height:2;color:#444}
.btn-teal{position:absolute;left:0;top:201px;background:var(--teal);color:var(--white);font-size:13px;font-weight:700;padding:10px 20px;border-radius:5px}
.about .photo{position:absolute;left:450px;top:2px;width:428px;height:270px;background:linear-gradient(135deg,#d7d6d2,#a8a49d 55%,#6a6d72)}

/* vision */
.vision{top:969px;height:299px;background:linear-gradient(90deg,#4f88b8,#6ea2cc 50%,#5d93c1)}
.vision .title{position:absolute;left:0;width:100%;top:10px;text-align:center;color:var(--white)}
.vbox{position:absolute;top:68px;width:344px;height:202px;border:1.5px solid var(--white);color:var(--white);text-align:center;font-size:12.5px;font-weight:600;line-height:2.2;padding:22px 30px 0}
.vbox .mini{position:absolute;left:50%;transform:translateX(-50%);bottom:16px;background:var(--white);color:var(--teal);font-size:11px;padding:6px 14px;border-radius:4px;line-height:1.2}

/* services */
.services{top:1290px;height:450px}
.services .title{position:absolute;left:0;width:100%;top:0;text-align:center;font-size:30px}
.services .rule{position:absolute;left:409px;top:46px}
.svc{position:absolute;width:200px;text-align:center;padding-top:24px}
.svc.hl{background:var(--teal-soft);height:180px}
.svc h3{font-family:"Lato",Arial,sans-serif;font-weight:400;font-size:19px;line-height:1.3;color:#333;height:50px}
.svc .bar{width:60px;height:3px;background:var(--green);margin:10px auto 14px}
.svc p{font-size:11.5px;line-height:2;color:var(--muted)}

/* conditions */
.conditions{top:1764px;height:299px;background:linear-gradient(90deg,#7ec7d2,#94d2da 50%,#82c9d3)}
.conditions .title{position:absolute;left:0;width:100%;top:12px;text-align:center;color:var(--white)}
.cond{position:absolute;display:flex;align-items:center;gap:12px;font-size:14px;font-weight:700;color:var(--white)}
.tick{width:28px;height:28px;background:var(--white);border-radius:4px;display:flex;align-items:center;justify-content:center}
.conditions .more{position:absolute;left:50%;transform:translateX(-50%);top:243px;background:var(--white);color:var(--teal);font-size:13px;font-weight:700;padding:9px 17px;border-radius:5px}

/* contact */
.contact{position:absolute;top:2092px;left:0;width:600px;height:302px;background:var(--panel)}
.contact h2{position:absolute;left:235px;top:20px;font-family:"Lato",Arial,sans-serif;font-weight:400;font-size:23px}
.contact .rule{position:absolute;left:235px;top:58px;width:56px}
.contact .ask{position:absolute;left:235px;top:87px;font-size:13.5px;font-weight:600}
.contact .line{position:absolute;left:235px;display:flex;align-items:center;gap:8px;font-size:9.5px;line-height:1.7;color:#444}
.contact .line .ic{width:36px;height:36px;border-radius:50%;background:var(--teal);display:flex;align-items:center;justify-content:center}
.contact .note{position:absolute;left:235px;top:246px;width:220px;font-size:9.5px;line-height:1.5;color:#444}
.appoint{position:absolute;top:2092px;left:600px;width:600px;height:302px;background:var(--blue);color:var(--white)}
.appoint h2{position:absolute;left:73px;top:20px;font-family:"Lato",Arial,sans-serif;font-weight:400;font-size:23px}
.appoint .rule{position:absolute;left:73px;top:58px;width:56px}
.field{position:absolute;width:138px;height:22px;border-bottom:1px solid var(--teal);font-size:9.5px}
.field .caret{position:absolute;right:2px;top:1px;font-size:8px;color:var(--teal)}
.send{position:absolute;left:73px;top:249px;background:#0f4e82;font-size:10px;font-weight:700;padding:5px 14px;border-radius:4px}

/* footer */
.footer{position:absolute;top:2394px;left:0;width:1200px;height:239px;background:var(--dark);color:var(--white)}
.fcol{position:absolute;top:22px}
.fcol h4{font-family:"Lato",Arial,sans-serif;font-weight:700;font-size:16px}
.fcol .rule{width:58px;margin-top:10px}
.fcol p{font-size:13px;line-height:1.8;margin-top:22px;width:180px}
.fcol em{display:block;font-weight:700;font-size:13px;margin-top:14px}
.fcol .dots{display:flex;gap:10px;margin-top:10px}
.fcol .dots span{width:12px;height:12px;border-radius:50%;background:var(--white)}
.fcol li{list-style:none;font-size:12.5px;width:200px;padding:9px 0 9px;border-bottom:1px solid var(--teal)}
.fcol li::before{content:"- ";color:#bbb}
.fcol .sched li{border-bottom:none;padding:7px 0}
.copy{position:absolute;top:2633px;left:0;width:1200px;height:54px;background:var(--darker);color:var(--white);font-size:12px;font-weight:700;text-align:center;line-height:54px;border-top:1px solid #666}
</style>
</head>
<body>

<div class="topbar">
  <div class="links"><span>Contact us</span><span>About us</span><span>Faqs</span><span>Online payment</span><span>Our providers</span></div>
  <div class="social"><span></span><span></span><span></span><span></span></div>
</div>

<header class="header">
  <div class="logo"><span class="dot"></span><span class="brand">Maplecrest Behavioral Healthcare</span></div>
  <div class="info" style="left:563px">
    <span class="ic"><svg width="14" height="20" viewBox="0 0 14 20"><rect x="1" y="1" width="12" height="18" rx="2" fill="none" stroke="#fff" stroke-width="2"/><circle cx="7" cy="15.5" r="1.2" fill="#fff"/></svg></span>
    <div><b>Phone:</b> (770) 555-0148<br><b>Fax:</b> (678) 555-0192</div>
  </div>
  <div class="info" style="left:733px">
    <span class="ic"><svg width="16" height="20" viewBox="0 0 16 20"><path d="M8 1a7 7 0 0 1 7 7c0 5-7 11-7 11S1 13 1 8a7 7 0 0 1 7-7z" fill="#fff"/><circle cx="8" cy="8" r="2.6" fill="#16b2c7"/></svg></span>
    <div><b>Birchwood Ave Ste 210</b><br>Fayetteville, GA 30299</div>
  </div>
  <div class="info" style="left:918px">
    <span class="ic"><svg width="18" height="18" viewBox="0 0 18 18"><rect x="1" y="3" width="16" height="14" rx="2" fill="none" stroke="#fff" stroke-width="2"/><path d="M1 7h16M5 1v4M13 1v4" stroke="#fff" stroke-width="2"/></svg></span>
    <div><b>8:00am-5:00pm</b><br>Monday-Friday</div>
  </div>
</header>

<nav class="nav">
  <ul><li class="active">Home</li><li>About Us</li><li>Services</li><li>Conditions We Treat</li><li>New Patients</li><li>Prescription Refills</li></ul>
  <svg class="search" width="18" height="18" viewBox="0 0 18 18"><circle cx="7.5" cy="7.5" r="5.5" fill="none" stroke="#fff" stroke-width="2"/><path d="M11.5 11.5l5 5" stroke="#fff" stroke-width="2"/></svg>
</nav>

<section class="hero" role="img" aria-label="Photo of a woman standing in a field of yellow wildflowers under a cloudy sky">
  <h1>Maplecrest Behavioral Healthcare</h1>
  <p>A step forward in your wellness journey</p>
  <span class="btn-green">Make an appointment</span>
  <div class="slider"><span></span><span></span><span class="on"></span></div>
</section>

<section class="wrap about">
  <h2 class="title">About Us</h2>
  <div class="rule"></div>
  <p>Since 2003 we have cared for children, adults and families in Fayetteville with warm, practical outpatient mental health support for every stage of life.</p>
  <span class="btn-teal">See More</span>
  <div class="photo" role="img" aria-label="Photo of a counselor talking with a patient in a bright office"></div>
</section>

<section class="wrap vision" role="img" aria-label="Blue tinted photo of a group therapy conversation">
  <h2 class="title">Vision &amp; Mission</h2>
  <div class="vbox" style="left:57px">To be the leading provider of outpatient psychiatric care in Atlanta Metro South, working together to promote (the) mental wellness of our community<span class="mini">See More</span></div>
  <div class="vbox" style="left:477px">To provide mental health services to children, adults, and the developmentally disabled population that is culturally sensitive regardless of age, race, gender, orientation, religion, or creed<span class="mini">See More</span></div>
</section>

<section class="wrap services">
  <h2 class="title">Our Services</h2>
  <div class="rule"></div>
  <div class="svc" style="left:0;top:80px"><h3>Diagnostic evaluation and treatment</h3><div class="bar"></div><p>Careful review of needs<br>and a clear plan</p></div>
  <div class="svc hl" style="left:226px;top:80px"><h3>Psychopharma cology</h3><div class="bar"></div><p>Thoughtful medication<br>care and follow up</p></div>
  <div class="svc" style="left:450px;top:80px"><h3>Bariatric pre-surgical consultation</h3><div class="bar"></div><p>Readiness checks before<br>weight loss surgery</p></div>
  <div class="svc" style="left:674px;top:80px"><h3>Disability and work-related reports</h3><div class="bar"></div><p>Detailed reports for work<br>and benefit claims</p></div>
  <div class="svc" style="left:111px;top:292px"><h3>Early childhood Assessments</h3><div class="bar"></div><p>Gentle screening for<br>our youngest patients</p></div>
  <div class="svc" style="left:335px;top:292px"><h3>Substance abuse assessments</h3><div class="bar"></div><p>Honest review and<br>steps toward recovery</p></div>
  <div class="svc" style="left:559px;top:292px"><h3>Developmental disabilities</h3><div class="bar"></div><p>Support for patients<br>and their families</p></div>
</section>

<section class="wrap conditions" role="img" aria-label="Teal tinted photo of a young woman in a counseling session">
  <h2 class="title">Conditions We Treat</h2>
  <div class="cond" style="left:93px;top:85px"><span class="tick"><svg width="18" height="14" viewBox="0 0 18 14"><path d="M2 7l5 5L16 2" fill="none" stroke="#f2c500" stroke-width="3"/></svg></span>Mood Disorders: Depression, Bipolar</div>
  <div class="cond" style="left:93px;top:130px"><span class="tick"><svg width="18" height="14" viewBox="0 0 18 14"><path d="M2 7l5 5L16 2" fill="none" stroke="#f2c500" stroke-width="3"/></svg></span>Anxiety Disorders: Generalized Anxiety..</div>
  <div class="cond" style="left:93px;top:174px"><span class="tick"><svg width="18" height="14" viewBox="0 0 18 14"><path d="M2 7l5 5L16 2" fill="none" stroke="#f2c500" stroke-width="3"/></svg></span>Common Disorders of Childhood: ADHD..</div>
  <div class="cond" style="left:459px;top:85px"><span class="tick"><svg width="18" height="14" viewBox="0 0 18 14"><path d="M2 7l5 5L16 2" fill="none" stroke="#f2c500" stroke-width="3"/></svg></span>Sleep Issues</div>
  <div class="cond" style="left:459px;top:130px"><span class="tick"><svg width="18" height="14" viewBox="0 0 18 14"><path d="M2 7l5 5L16 2" fill="none" stroke="#f2c500" stroke-width="3"/></svg></span>Psychotic Disorders: Schizophrenia</div>
  <div class="cond" style="left:459px;top:174px"><span class="tick"><svg width="18" height="14" viewBox="0 0 18 14"><path d="M2 7l5 5L16 2" fill="none" stroke="#f2c500" stroke-width="3"/></svg></span>And More: Addiction, Eating Disorders</div>
  <span class="more">See More</span>
</section>

<section class="contact">
  <h2>Contact Info</h2>
  <div class="rule"></div>
  <p class="ask">Need to discuss before treatment?</p>
  <div class="line" style="top:123px"><span class="ic"><svg width="12" height="18" viewBox="0 0 14 20"><rect x="1" y="1" width="12" height="18" rx="2" fill="none" stroke="#fff" stroke-width="2"/><circle cx="7" cy="15.5" r="1.2" fill="#fff"/></svg></span><div><b>Phone:</b> (770) 555-0148<br><b>Fax:</b> (678) 555-0192</div></div>
  <div class="line" style="top:178px"><span class="ic"><svg width="14" height="18" viewBox="0 0 16 20"><path d="M8 1a7 7 0 0 1 7 7c0 5-7 11-7 11S1 13 1 8a7 7 0 0 1 7-7z" fill="#fff"/><circle cx="8" cy="8" r="2.6" fill="#16b2c7"/></svg></span><div><b>Birchwood Ave Ste 210</b><br>Fayetteville, GA 30299</div></div>
  <p class="note">Call during office hours and our front desk team will gladly help you.</p>
</section>

<section class="appoint">
  <h2>Fix An Appointment</h2>
  <div class="rule"></div>
  <div class="field" style="left:73px;top:92px">Your Name</div>
  <div class="field" style="left:233px;top:92px">Email</div>
  <div class="field" style="left:73px;top:133px">Phone</div>
  <div class="field" style="left:233px;top:133px">Date<span class="caret">&#9660;</span></div>
  <div class="field" style="left:73px;top:174px;height:62px">Message</div>
  <div class="field" style="left:233px;top:174px">Service<span class="caret">&#9660;</span></div>
  <span class="send">Send</span>
</section>

<footer class="footer">
  <div class="fcol" style="left:231px">
    <h4>ABOUT US</h4><div class="rule"></div>
    <p>Caring outpatient support for every age, close to home.</p>
    <em>FOLLOW US</em>
    <div class="dots"><span></span><span></span><span></span></div>
  </div>
  <div class="fcol" style="left:476px">
    <h4>OUR SERVICES</h4><div class="rule"></div>
    <ul style="margin-top:12px"><li>Early childhood Assessments</li><li>Psychopharmacology</li><li>Diagnostic evaluation</li><li>Bariatric pre-surgical consultation</li></ul>
  </div>
  <div class="fcol" style="left:770px">
    <h4>OUR TIME SCHEDULE</h4><div class="rule"></div>
    <ul class="sched" style="margin-top:12px"><li>Monday - Thursday</li><li style="border-bottom:1px solid var(--teal)">8:00 Am - 5:00 Pm</li><li>Friday</li><li style="padding-left:10px">8:00 Am - 1:00 Pm</li></ul>
  </div>
</footer>
<div class="copy">Maplecrest Behavioral Healthcare &copy; 2017. All Rights Reserved</div>

</body>
</html>
```